Brivolt Technologies business card design

We need a business card designed with our new logo. it would be great if the card could communicate it is a technology based company.

Target Market(s)

system integrators

Industry/Entity Type

technology, IOT

Contact Information for Business Card

Name, designation, Address, telephone number, email address

Requirements
Must have
• logo and company name
Nice to have
• something to do with technology

```html
<!DOCTYPE html>
<html lang="en">
<head>
<meta charset="utf-8">
<title>Brivolt Technologies Business Card</title>
<link rel="stylesheet" href="https://fonts.googleapis.com/css2?family=Open+Sans:ital,wght@0,400;0,700;0,800;1,400&display=swap">
<style>
  :root {
    --stage: #2a2a2a;
    --card: #151515;
    --card-deep: #0c0c0c;
    --orange: #f7931e;
    --white: #ffffff;
    --text-soft: #e6e6e6;
    --shade: #2b2b2b;
  }
  * { box-sizing: border-box; margin: 0; padding: 0; }
  html, body {
    width: 1200px; height: 900px; overflow: hidden;
    background: var(--stage);
    font-family: "Open Sans", Arial, sans-serif;
  }
  .canvas {
    width: 1200px; height: 900px;
    display: flex; flex-direction: column; align-items: center; justify-content: center;
    gap: 36px;
  }
  .card {
    position: relative;
    width: 700px; height: 400px;
    background: var(--card);
    border-bottom: 3px solid var(--orange);
    border-right: 3px solid var(--orange);
    overflow: hidden;
    box-shadow: 0 14px 30px rgba(0,0,0,.5);
  }
  .brand {
    position: absolute; display: flex; align-items: center; gap: 14px;
  }
  .brand-mark { width: 22px; height: 22px; background: var(--orange); }
  .brand-name {
    color: var(--white); font-weight: 800; font-size: 34px;
    letter-spacing: .5px; text-transform: uppercase; line-height: 1;
  }
  .card-front .brand { left: 48px; top: 52px; }
  .address {
    position: absolute; left: 48px; top: 140px;
    color: var(--text-soft); font-size: 17px; line-height: 1.45;
  }
  .contacts {
    position: absolute; left: 48px; top: 218px;
    list-style: none; color: var(--text-soft); font-size: 17px; line-height: 1.55;
  }
  .contacts li { display: flex; align-items: center; gap: 10px; }
  .contacts svg { width: 14px; height: 14px; fill: var(--orange); flex: none; }
  .holder {
    position: absolute; right: 48px; top: 150px; text-align: right;
  }
  .holder-name {
    color: var(--orange); font-weight: 700; font-size: 26px;
    text-transform: uppercase; letter-spacing: .5px;
  }
  .holder-role { color: var(--text-soft); font-size: 19px; }
  .front-graphic {
    position: absolute; right: 40px; bottom: 0;
    width: 330px; height: 150px;
    background: linear-gradient(160deg, var(--card-deep) 0%, var(--shade) 100%);
  }
  .back-pattern {
    position: absolute; inset: 0;
    background: linear-gradient(135deg, var(--card-deep) 0%, var(--shade) 50%, var(--card-deep) 100%);
  }
  .card-back .brand { right: 40px; bottom: 36px; }
  .card-back .brand-name { font-size: 24px; }
  .card-back .brand-mark { width: 16px; height: 16px; }
</style>
</head>
<body>
<main class="canvas">
  <section class="card card-front">
    <div class="brand">
      <span class="brand-mark"></span>
      <span class="brand-name">Brivolt Technologies</span>
    </div>
    <p class="address">18420 Harbor Crest Dr<br>Seacliff CA 92700</p>
    <ul class="contacts">
      <li><svg viewBox="0 0 16 16"><path d="M3 1h3l1.5 4-2 1.3a9 9 0 0 0 4.2 4.2L11 8.5l4 1.5v3a2 2 0 0 1-2 2A12 12 0 0 1 1 3a2 2 0 0 1 2-2z"/></svg>555-301-7782</li>
      <li><svg viewBox="0 0 16 16"><path d="M1 3h14v10H1z M1 3l7 6 7-6" fill="none" stroke="#f7931e" stroke-width="1.6"/></svg>info@brivolttechnologies.com</li>
      <li><svg viewBox="0 0 16 16"><circle cx="8" cy="8" r="6.5" fill="none" stroke="#f7931e" stroke-width="1.6"/><path d="M1.5 8h13M8 1.5c-3 3.5-3 9.5 0 13M8 1.5c3 3.5 3 9.5 0 13" fill="none" stroke="#f7931e" stroke-width="1.2"/></svg>www.brivolttechnologies.com</li>
    </ul>
    <div class="holder">
      <p class="holder-name">Daren Holvik</p>
      <p class="holder-role">President</p>
    </div>
    <div class="front-graphic" role="img" aria-label="Large faint dark company symbol as corner decoration"></div>
  </section>

  <section class="card card-back">
    <div class="back-pattern" role="img" aria-label="Repeating dark tone-on-tone pattern of the company symbol"></div>
    <div class="brand">
      <span class="brand-mark"></span>
      <span class="brand-name">Brivolt Technologies</span>
    </div>
  </section>
</main>
</body>
</html>
```